Logistics Website Design

See website https://tqfreightglobal.com for theme and color details. Need the site to be re-done and reflect some of the designs shown in this list here: https://pixelvane.com/tags/logistics-company-website

Target Market(s)

Logistics & Transportation

Industry/Entity Type

Logistics and Supply Chain

Coding

Number of Pages Required

5+ page

Requirements
Must have
• Colors must match theme of logo. Looking for a sleek, interactive design.

```html
<!DOCTYPE html>
<html lang="en">
<head>
<meta charset="utf-8">
<title>TQ Freight Global — Logistics & Transportation</title>
<link rel="stylesheet" href="https://fonts.googleapis.com/css2?family=Inter:ital,wght@0,400;0,500;0,600;0,700;0,800;1,400;1,500&display=swap">
<style>
  :root{
    --bg-deep:#220f07;
    --bg-brown:#3a1e12;
    --orange:#e8603a;
    --orange-soft:#c96a44;
    --card-line:#5b3322;
    --text:#ffffff;
    --text-dim:#efe4de;
    --star:#f5a623;
  }
  *{box-sizing:border-box;margin:0;padding:0}
  html,body{width:1200px;height:2997px;overflow:hidden}
  body{background:var(--bg-deep);color:var(--text);font-family:"Inter",sans-serif;position:relative}
  .abs{position:absolute}

  /* Hero */
  .hero-photo{left:0;top:0;width:1200px;height:740px;
    background:
      radial-gradient(ellipse 420px 300px at 560px 330px, rgba(220,120,60,.55), transparent 70%),
      linear-gradient(100deg,#2a130a 0%,#4a2614 32%,#8a5232 55%,#6b4a44 75%,#4b3a3e 100%)}
  .hero-shade{left:0;top:0;width:1200px;height:740px;
    background:linear-gradient(90deg,rgba(34,15,7,.75) 0%,rgba(34,15,7,.35) 45%,rgba(34,15,7,0) 70%)}
  .hero-curve{left:0;top:600px}

  .brand{display:flex;align-items:center;gap:10px}
  .brand-mark{width:46px;height:46px;border-radius:50%;background:var(--orange)}
  .brand-name{font-weight:800;font-size:19px;letter-spacing:.5px;color:var(--text);text-transform:uppercase}
  .header-brand{left:110px;top:58px}

  .nav{display:flex;font-size:14.5px;letter-spacing:.3px}
  .nav a{color:var(--text);text-decoration:none;position:absolute;white-space:nowrap}
  .nav a.active{font-weight:700}
  .main-nav{left:0;top:31px}
  .nav-underline{left:410px;top:64px;width:63px;height:3px;background:var(--orange);border-radius:2px}

  .btn{background:var(--orange);color:var(--text);border-radius:30px;font-weight:700;display:flex;align-items:center;justify-content:center;text-decoration:none;text-transform:uppercase}
  .btn-header{left:943px;top:24px;width:144px;height:33px;font-size:14px;text-transform:none}

  .hero-title{left:106px;top:236px;font-size:52px;line-height:61px;font-weight:800;letter-spacing:.5px}
  .hero-sub{left:106px;top:373px;font-size:22px;font-weight:400}
  .btn-hero{left:102px;top:440px;width:264px;height:44px;font-size:19px}
  .dots{left:108px;top:553px;display:flex;gap:14px}
  .dots span{width:7px;height:7px;border-radius:50%;background:#c98a6a}

  /* Services */
  .section-title{width:1200px;text-align:center;font-weight:700;font-size:53px;left:0}
  .services-title{top:722px}
  .title-rule{left:500px;top:795px;width:200px;height:1px;background:#5a3a2c}
  .title-rule-accent{left:563px;top:794px;width:75px;height:4px;background:var(--orange);border-radius:2px}

  .card{top:840px;width:319px;height:421px;border:1px solid var(--card-line);border-radius:12px;text-align:center}
  .card.featured{border:none;background:linear-gradient(160deg,#7a3f26 0%,#a05535 55%,#c06a48 100%)}
  .card-icon{position:absolute;left:105px;top:30px;width:108px;height:108px;border-radius:50%;border:1.5px solid #7a4630;background:#2c150b}
  .card.featured .card-icon{background:#2a1209;border-color:#2a1209}
  .card-title{position:absolute;left:0;top:160px;width:100%;font-size:28px;line-height:33px;font-weight:700}
  .card-text{position:absolute;left:18px;top:239px;width:283px;font-size:13.5px;line-height:21.5px;color:var(--text-dim)}
  .card-arrow{position:absolute;left:137px;top:347px;width:44px;height:44px;border-radius:50%;border:1.5px solid #7a4630;display:flex;align-items:center;justify-content:center}
  .card.featured .card-arrow{background:#2a1209;border-color:#2a1209}

  /* About band */
  .about-band{left:0;top:1412px;width:1200px;height:630px;background:var(--bg-brown)}
  .about-photo{left:0;top:1398px}
  .about-title{left:100px;top:1502px;font-size:48px;line-height:57px;font-weight:700}
  .about-rule{left:100px;top:1622px;width:200px;height:1px;background:#7a5444}
  .about-rule-accent{left:100px;top:1621px;width:139px;height:4px;background:var(--orange);border-radius:2px}
  .about-text{left:100px;top:1637px;width:450px;font-size:14.8px;line-height:25.5px;color:var(--text-dim)}
  .btn-about{left:101px;top:1811px;width:187px;height:44px;font-size:19px}

  /* Testimonials */
  .testi-title{top:2122px}
  .avatar{border-radius:50%;border:2px solid #f3e6de;background:linear-gradient(160deg,#b88a72,#5e3a2a)}
  .quote{left:100px;top:2363px;width:1000px;text-align:center;font-style:italic;font-size:22px;line-height:25.5px}
  .quote-name{left:0;width:1200px;top:2449px;text-align:center;font-size:27px;font-weight:600}
  .stars{left:552px;top:2497px;display:flex;gap:2px}
  .pager{left:580px;top:2551px;display:flex;gap:13px}

  /* Footer */
  .footer{left:0;top:2660px;width:1200px;height:337px;background:var(--bg-brown)}
  .footer-brand{left:0;top:2730px;width:1200px;justify-content:center}
  .social{top:2899px;left:0;width:1200px;display:flex;justify-content:center;gap:18px}
  .social span{width:14px;height:14px;border-radius:50%;background:#f3e6de}
  .copyright{left:0;top:2945px;width:1200px;text-align:center;font-size:14.5px}
</style>
</head>
<body>

  <!-- Hero -->
  <div class="abs hero-photo" role="img" aria-label="Semi truck with shipping container driving at a port at sunset"></div>
  <div class="abs hero-shade"></div>
  <svg class="abs hero-curve" width="1200" height="145" viewBox="0 0 1200 145" aria-hidden="true">
    <path d="M0 132 C200 40 420 26 600 28 C820 30 1020 60 1200 132 L1200 145 L0 145 Z" fill="#220f07"/>
  </svg>

  <div class="abs brand header-brand">
    <span class="brand-mark"></span>
    <span class="brand-name">TQ Freight Global</span>
  </div>

  <nav class="abs nav main-nav">
    <a class="active" href="#" style="left:418px">HOME</a>
    <a href="#" style="left:497px">SERVICES</a>
    <a href="#" style="left:601px">INDUSTRIES</a>
    <a href="#" style="left:722px">ABOUT US</a>
    <a href="#" style="left:831px">CONTACT</a>
  </nav>
  <div class="abs nav-underline"></div>
  <a class="abs btn btn-header" href="#">Request a Quote</a>

  <h1 class="abs hero-title">DELIVERING STRENGTH<br>IN EVERY MILE</h1>
  <p class="abs hero-sub">Secure and reliable transportation for all your cargo needs.</p>
  <a class="abs btn btn-hero" href="#">Request a Quote</a>
  <div class="abs dots"><span></span><span></span><span></span><span></span></div>

  <!-- Services -->
  <h2 class="abs section-title services-title">Our Services</h2>
  <div class="abs title-rule"></div>
  <div class="abs title-rule-accent"></div>

  <article class="abs card" style="left:102px">
    <div class="card-icon" role="img" aria-label="Flatbed truck icon"></div>
    <h3 class="card-title">Flatbed<br>Transportation</h3>
    <p class="card-text">From routine shipments to oversized and heavy-haul loads, we handle freight requiring proper securement, regulatory knowledge, and consistent on-time execution.</p>
    <div class="card-arrow"><svg width="16" height="16" viewBox="0 0 16 16"><path d="M3 13 L13 3 M6 3 H13 V10" stroke="#fff" stroke-width="2" fill="none" stroke-linecap="round"/></svg></div>
  </article>

  <article class="abs card featured" style="left:441px">
    <div class="card-icon" role="img" aria-label="Step deck truck icon"></div>
    <h3 class="card-title">Step Deck<br>Transportation</h3>
    <p class="card-text">Our step deck trucking services support tall, heavy, and specialized freight that requires additional height clearance and flexible loading options.</p>
    <div class="card-arrow"><svg width="16" height="16" viewBox="0 0 16 16"><path d="M3 13 L13 3 M6 3 H13 V10" stroke="#fff" stroke-width="2" fill="none" stroke-linecap="round"/></svg></div>
  </article>

  <article class="abs card" style="left:779px">
    <div class="card-icon" role="img" aria-label="Dry van truck icon"></div>
    <h3 class="card-title">Dry Van<br>Transportation</h3>
    <p class="card-text">From consumer goods to industrial materials, our dry van services provide the space, security, and consistency you need coast to coast.</p>
    <div class="card-arrow"><svg width="16" height="16" viewBox="0 0 16 16"><path d="M3 13 L13 3 M6 3 H13 V10" stroke="#fff" stroke-width="2" fill="none" stroke-linecap="round"/></svg></div>
  </article>

  <!-- About band -->
  <div class="abs about-band"></div>
  <svg class="abs about-photo" width="1200" height="644" viewBox="0 0 1200 644" role="img" aria-label="Orange semi truck with container trailer on a wet port road">
    <defs>
      <linearGradient id="photoTone" x1="0" y1="0" x2="0" y2="1">
        <stop offset="0" stop-color="#9fb3c6"/>
        <stop offset=".45" stop-color="#b9a596"/>
        <stop offset=".7" stop-color="#a8553a"/>
        <stop offset="1" stop-color="#3d3b3c"/>
      </linearGradient>
    </defs>
    <polygon points="637,0 1200,0 1200,14 647,14 570,644 549,630" fill="#7a3f1f"/>
    <polygon points="647,14 1200,14 1200,644 570,644" fill="url(#photoTone)"/>
  </svg>

  <h2 class="abs about-title">Keeping Your Supply<br>Chain Moving</h2>
  <div class="abs about-rule"></div>
  <div class="abs about-rule-accent"></div>
  <p class="abs about-text">We deliver a comprehensive range of open-deck and specialized transportation services—including flatbed, step deck, heavy haul, and over-dimensional freight solutions. Backed by years of experience, a trusted nationwide carrier network, and a strong safety-first culture, we provide reliable, adaptable logistics support built around the unique requirements of every load.</p>
  <a class="abs btn btn-about" href="#">Learn More</a>

  <!-- Testimonials -->
  <h2 class="abs section-title testi-title">Testimonials</h2>
  <div class="abs avatar" style="left:378px;top:2248px;width:74px;height:74px" role="img" aria-label="Client portrait"></div>
  <div class="abs avatar" style="left:464px;top:2248px;width:74px;height:74px" role="img" aria-label="Client portrait"></div>
  <div class="abs avatar" style="left:549px;top:2235px;width:100px;height:100px" role="img" aria-label="Portrait of Lina, featured client"></div>
  <div class="abs avatar" style="left:661px;top:2248px;width:74px;height:74px" role="img" aria-label="Client portrait"></div>
  <div class="abs avatar" style="left:747px;top:2248px;width:74px;height:74px" role="img" aria-label="Client portrait"></div>

  <p class="abs quote">“Lorem ipsum dolor sit amet, consectetur adipiscing elit, sed do eiusmod tempor incididunt ut labore et dolore magna aliqua. Quis ipsum suspendisse ultrices gravida. Risus commodo viverra maecenas accumsan lacus vel facilisis.”</p>
  <p class="abs quote-name">-Lina</p>
  <div class="abs stars" aria-label="5 out of 5 stars">
    <svg width="96" height="20" viewBox="0 0 96 20">
      <g fill="#f5a623">
        <path id="st" d="M9.5 1 L12 7 L18.5 7.3 L13.4 11.4 L15.2 18 L9.5 14.3 L3.8 18 L5.6 11.4 L0.5 7.3 L7 7 Z"/>
        <use href="#st" x="19"/><use href="#st" x="38"/><use href="#st" x="57"/><use href="#st" x="76"/>
      </g>
    </svg>
  </div>
  <div class="abs pager">
    <svg width="12" height="16" viewBox="0 0 12 16"><path d="M8 2 L3 8 L8 14" stroke="#fff" stroke-width="2" fill="none" stroke-linecap="round"/></svg>
    <svg width="12" height="16" viewBox="0 0 12 16"><path d="M4 2 L9 8 L4 14" stroke="#fff" stroke-width="2" fill="none" stroke-linecap="round"/></svg>
  </div>

  <!-- Footer -->
  <footer class="abs footer"></footer>
  <div class="abs brand footer-brand">
    <span class="brand-mark"></span>
    <span class="brand-name">TQ Freight Global</span>
  </div>
  <nav class="abs nav" style="left:0;top:2845px">
    <a class="active" href="#" style="left:358px">HOME</a>
    <a href="#" style="left:438px">SERVICES</a>
    <a href="#" style="left:542px">INDUSTRIES</a>
    <a href="#" style="left:663px">ABOUT US</a>
    <a href="#" style="left:772px">CONTACT</a>
  </nav>
  <div class="abs social" aria-label="Social links">
    <span aria-label="Social profile 1"></span>
    <span aria-label="Social profile 2"></span>
    <span aria-label="Social profile 3"></span>
    <span aria-label="Social profile 4"></span>
  </div>
  <p class="abs copyright">© 2026 &nbsp;|&nbsp; www.tqfreightglobal.com</p>

</body>
</html>
```